Business card for law firm

Need business card for new law firm. Think confident, authoritative, conservative, but not stuffy or old-fashioned.

Contact Information for Business Card

Content for card - logo (uploaded), plus the following:

Paul Whitcombe (larger font)
Managing Partner (larger font, but not as large as name)
Level 9, 7 Ferris Lane
Sydney NSW 2000
Main Tel 02 9364 2710
Direct Tel 02 8472 3159
Email paul@qvlegal.com.au
www.qvlegal.com.au

Letterhead design should include logo plus:
Level 9, 7 Ferris Lane
Sydney NSW 2000
Tel 02 8472 3159
www.qvlegal.com.au

```html
<!DOCTYPE html>
<html lang="en">
<head>
<meta charset="utf-8">
<title>Quayvale Lawyers – Business Card</title>
<link rel="stylesheet" href="https://fonts.googleapis.com/css2?family=Open+Sans:wght@400;700&display=swap">
<style>
  :root {
    --navy: #001a57;
    --ink: #111111;
    --white: #ffffff;
    --bg-light: #ececed;
    --bg-dark: #c4c5c8;
    --card-edge: #b9b9bb;
    --strip: #000000;
  }
  * { box-sizing: border-box; margin: 0; padding: 0; }
  html, body { width: 1200px; height: 1142px; overflow: hidden; }
  body {
    position: relative;
    background: linear-gradient(160deg, var(--bg-light) 0%, #d9dadc 45%, var(--bg-dark) 100%);
    font-family: "Open Sans", Arial, sans-serif;
  }
  .card {
    position: absolute;
    width: 758px;
    height: 433px;
    border-radius: 34px;
    overflow: hidden;
  }
  .card--front {
    left: 77px; top: 95px;
    background: var(--white);
    border: 1.5px solid var(--card-edge);
  }
  .card--back {
    left: 337px; top: 590px;
    background: var(--navy);
  }

  /* firm name placeholder */
  .firm-name {
    position: absolute;
    display: flex;
    align-items: center;
    gap: 12px;
    font-family: "Open Sans", Arial, sans-serif;
    font-weight: 400;
    white-space: nowrap;
    line-height: 1;
  }
  .firm-name__square { width: 26px; height: 26px; flex: none; }
  .card--front .firm-name {
    left: 40px; top: 200px;
    width: 330px;
    justify-content: center;
    font-size: 30px;
    color: var(--navy);
  }
  .card--front .firm-name__square { background: var(--navy); }
  .card--back .firm-name {
    left: 48px; top: 70px;
    font-size: 36px;
    color: var(--white);
  }
  .card--back .firm-name__square { background: var(--white); width: 30px; height: 30px; }

  /* web strip */
  .web-strip {
    position: absolute;
    left: 403px; top: 63px;
    width: 34px; height: 304px;
    background: var(--strip);
  }
  .web-strip__text {
    position: absolute;
    left: 50%; top: 50%;
    transform: translate(-50%, -50%) rotate(-90deg);
    white-space: nowrap;
    color: var(--white);
    font-size: 19px;
    letter-spacing: 2.4px;
  }

  /* contact panel */
  .contact-panel {
    position: absolute;
    left: 444px; top: 63px;
    width: 314px; height: 304px;
    background: var(--navy);
    color: var(--white);
    padding: 20px 0 0 21px;
  }
  .contact-panel__name { font-size: 25px; font-weight: 700; line-height: 1.2; letter-spacing: 0.3px; }
  .contact-panel__role { font-size: 19px; line-height: 1.2; margin-top: 5px; }
  .contact-list { list-style: none; margin-top: 17px; }
  .contact-list__item {
    display: flex; align-items: center;
    font-size: 19px; line-height: 33px;
  }
  .contact-list__icon { width: 16px; height: 16px; margin-right: 6px; flex: none; }
  .contact-panel__address { font-size: 19px; line-height: 31px; margin-top: 12px; }

  /* back web address */
  .back-web {
    position: absolute;
    right: 75px; top: 370px;
    color: var(--white);
    font-size: 23px;
    letter-spacing: 3.5px;
  }
  .back-web strong { font-weight: 700; }
</style>
</head>
<body>

  <section class="card card--front" aria-label="Business card front">
    <p class="firm-name">
      <span class="firm-name__square" aria-hidden="true"></span>
      Quayvale Lawyers
    </p>

    <div class="web-strip">
      <span class="web-strip__text">www.qvlegal.com.au</span>
    </div>

    <div class="contact-panel">
      <p class="contact-panel__name">PAUL WHITCOMBE</p>
      <p class="contact-panel__role">MANAGING PARTNER</p>
      <ul class="contact-list">
        <li class="contact-list__item">
          <svg class="contact-list__icon" viewBox="0 0 16 16" aria-hidden="true">
            <circle cx="8" cy="8" r="7" fill="none" stroke="#fff" stroke-width="1.3"/>
            <path d="M5.3 4.2l1.4 1.6-.8 1c.6 1.3 1.5 2.2 2.8 2.8l1-.8 1.6 1.4-.9 1.2C7.6 11.4 4.6 8.4 4.1 5.1z" fill="#fff"/>
          </svg>
          02 9364 2710(Main)
        </li>
        <li class="contact-list__item">
          <svg class="contact-list__icon" viewBox="0 0 16 16" aria-hidden="true">
            <circle cx="8" cy="8" r="7" fill="none" stroke="#fff" stroke-width="1.3"/>
            <path d="M5.3 4.2l1.4 1.6-.8 1c.6 1.3 1.5 2.2 2.8 2.8l1-.8 1.6 1.4-.9 1.2C7.6 11.4 4.6 8.4 4.1 5.1z" fill="#fff"/>
          </svg>
          02 8472 3159(Direct)
        </li>
        <li class="contact-list__item">
          <svg class="contact-list__icon" viewBox="0 0 16 16" aria-hidden="true">
            <path d="M1 6l7-4 7 4v8H1z" fill="#fff"/>
            <path d="M1.5 6.5L8 10.5l6.5-4" fill="none" stroke="#001a57" stroke-width="1.2"/>
          </svg>
          paul@qvlegal.com.au
        </li>
      </ul>
      <p class="contact-panel__address">Level 9, 7 Ferris Lane<br>Sydney NSW 2000</p>
    </div>
  </section>

  <section class="card card--back" aria-label="Business card back">
    <p class="firm-name">
      <span class="firm-name__square" aria-hidden="true"></span>
      Quayvale Lawyers
    </p>
    <p class="back-web">www.<strong>qvlegal</strong>.com.au</p>
  </section>

</body>
</html>
```